Laser Tattoo Removal Business Cards

We are looking for a professional business card design for a laser tattoo removal business. Ideally looking for a black business card design. The name of the business is Brightline Tattoo Removal. We place our cards at local tattoo shops so we ideally are looking for something trendy/edgy to draw both male and female clientele in.

Target Market(s)

Male/Female ages 18-60

Contact Information for Business Card

black background ideally.. hoping to stay within greys, whites and black

Font styles to use
Serif
Sans Serif

Colors
121212
a9a9a9
5c5c5c
f5f5f5
ffffff
7f7f7f
606060
848484
9d9d9d

Requirements
Must have
• Employee Info:
• Melissa Thornbury
• Chief Executive Offer
• m: 919.537.2846
• w: 919.362.4178
• f: 919.685.3907
• mthornbury@brightlinetattooremoval.example
• Address:
• 4615 Oakmere Pkwy, Suite 210
• Raleigh, NC 27654
• Website:
• www.brightlinetattooremoval.example
Nice to have
• Myabe business name on back or logo on back and employee info on the front

```html
<!DOCTYPE html>
<html lang="en">
<head>
<meta charset="utf-8">
<title>Brightline Tattoo Removal – Business Cards</title>
<link rel="stylesheet" href="https://fonts.googleapis.com/css2?family=Roboto:wght@400;500&family=Roboto+Condensed:wght@700&display=swap">
<style>
  :root {
    --card: #121212;
    --page: #5c5c5c;
    --white: #ffffff;
    --soft-white: #f5f5f5;
    --grey-light: #a9a9a9;
    --grey-mid: #848484;
    --grey-dark: #606060;
  }
  * { margin: 0; padding: 0; box-sizing: border-box; }
  html, body { width: 1200px; height: 769px; overflow: hidden; }
  body {
    background: var(--page);
    font-family: "Roboto", sans-serif;
    position: relative;
  }
  .card {
    position: absolute;
    top: 236px;
    width: 520px;
    height: 297px;
    background: var(--card);
    border-radius: 3px;
    color: var(--white);
  }
  .card--front { left: 50px; }
  .card--back { left: 630px; }

  /* Wordmark */
  .wordmark { position: absolute; font-family: "Roboto", sans-serif; font-weight: 500; color: var(--white); }
  .wordmark__name { display: block; letter-spacing: 2px; line-height: 1; }
  .wordmark__tag { display: block; letter-spacing: 3px; line-height: 1; }
  .card--front .wordmark { left: 30px; top: 92px; }
  .card--front .wordmark__name { font-size: 34px; }
  .card--front .wordmark__tag { font-size: 13px; margin-top: 14px; }
  .card--back .wordmark { left: 0; right: 0; top: 96px; text-align: center; }
  .card--back .wordmark__name { font-size: 36px; color: var(--soft-white); }
  .card--back .wordmark__tag { font-size: 14px; margin-top: 16px; color: var(--grey-light); }

  .rule { position: absolute; height: 1px; background: var(--grey-light); }
  .rule--name { left: 220px; right: 34px; top: 84px; }
  .rule--tag { left: 30px; width: 14px; top: 130px; }

  /* Employee */
  .employee { position: absolute; right: 34px; top: 38px; text-align: right; }
  .employee__name { font-family: "Roboto Condensed", sans-serif; font-weight: 700; font-size: 20px; letter-spacing: 0.3px; }
  .employee__title { font-size: 12px; color: var(--soft-white); margin-top: 2px; }
  .tab { position: absolute; right: 0; top: 40px; width: 12px; height: 28px; background: var(--white); }

  /* Contacts */
  .contacts { position: absolute; left: 30px; top: 168px; list-style: none; }
  .contacts li { display: flex; align-items: center; font-size: 12.5px; line-height: 17px; color: var(--soft-white); }
  .contacts svg { width: 11px; height: 11px; margin-right: 9px; fill: var(--white); flex: none; }

  .website { position: absolute; left: 0; right: 0; top: 198px; text-align: center; font-size: 12px; letter-spacing: 2.5px; color: var(--grey-light); }
</style>
</head>
<body>

<section class="card card--front">
  <div class="employee">
    <div class="employee__name">MELISSA THORNBURY</div>
    <div class="employee__title">Chief Executive Offer</div>
  </div>
  <div class="tab"></div>
  <div class="rule rule--name"></div>

  <div class="wordmark">
    <span class="wordmark__name">BRIGHTLINE</span>
    <span class="wordmark__tag">TATTOO REMOVAL</span>
  </div>

  <ul class="contacts">
    <li><svg viewBox="0 0 12 12"><path d="M2.5 1l2 2-1 1.3a7 7 0 0 0 4.2 4.2L9 7.5l2 2-1.5 1.5C5 11 1 7 1 2.5z"/></svg>w: 919.362.4178</li>
    <li><svg viewBox="0 0 12 12"><path d="M3 0.5h6v11H3zM4 1.5v7.5h4V1.5z"/></svg>m: 919.537.2846</li>
    <li><svg viewBox="0 0 12 12"><path d="M3 1h6v3H3zM1 4.5h10v5H9v2H3v-2H1zM4 8v2.5h4V8z"/></svg>f: 919.685.3907</li>
    <li><svg viewBox="0 0 12 12"><path d="M1 2.5h10v7H1zM2 3.5l4 3 4-3z"/></svg>mthornbury@brightlinetattooremoval.example</li>
    <li><svg viewBox="0 0 12 12"><circle cx="6" cy="6" r="5"/></svg>www.brightlinetattooremoval.example</li>
    <li><svg viewBox="0 0 12 12"><path d="M6 0.5a4 4 0 0 1 4 4c0 3-4 7-4 7s-4-4-4-7a4 4 0 0 1 4-4zm0 2.5a1.5 1.5 0 1 0 0 3 1.5 1.5 0 0 0 0-3z"/></svg>4615 Oakmere Pkwy, Suite 210, Raleigh, NC 27654</li>
  </ul>
</section>

<section class="card card--back">
  <div class="wordmark">
    <span class="wordmark__name">BRIGHTLINE</span>
    <span class="wordmark__tag">TATTOO REMOVAL</span>
  </div>
  <div class="website">www.brightlinetattooremoval.example</div>
</section>

</body>
</html>
```